Postcard for Construction Industry

www.brindlequants.com is our website.

We offer services to construction companies to read blueprints and give them a materials quantity list of how much work they need to do on a project. We service all types of companies such as painting, flooring, siding, drywall, Acoustical ceiling tile, framing, millwork, and much more.

I want a postcard designed that can be sent via email AND regular mail to introduce our company.

I've also attached another document with more detailed explanation, pricing, etc.

Important:
The postcard must appeal to the construction industry so they pick it up and read it.

Target Market(s)

Construction Industry

Industry/Entity Type

Construction

Font styles to use
Serif

Requirements
Must have
• Call to Action -
• Register on our site
• Get a FREE Quote
• Trades Serviced should be referenced on front so the person reading it immediately knows 2 things. Free Construction Takeoffs. List of Trades.
Nice to have
• Construction Images
• It's so EASY!!!
• -You load your plans
• -We give you a quote
• -If you approve, we do the work!
• NO OBLIGATION TO PURCHASE
Should not have
• Pricing - other than FREE Quotes
• Should not have phone number Prominent. It can be small on the back. (I want them to register via website)

```html
<!DOCTYPE html>
<html lang="en">
<head>
<meta charset="utf-8">
<title>Brindle Quants Postcard</title>
<link rel="stylesheet" href="https://fonts.googleapis.com/css2?family=Open+Sans:wght@400;600;700;800&display=swap">
<style>
:root{
  --ink:#0f2a4a;
  --navy:#13325a;
  --blue:#1d64ad;
  --sky:#3d8fdc;
  --pale:#9fd0ff;
  --text:#333b45;
  --paper:#ffffff;
  --stage:#0b0b0b;
}
*{margin:0;padding:0;box-sizing:border-box}
html,body{width:804px;height:1200px;overflow:hidden;background:var(--stage);font-family:"Open Sans",sans-serif}
.card{position:absolute;left:27px;width:750px;background:var(--paper);overflow:hidden}
.front{top:59px;height:590px}
.back{top:670px;height:510px}
.art{position:absolute;left:0;top:0}
.brand{position:absolute;left:28px;top:20px;display:flex;align-items:center;gap:10px}
.brand-mark{width:22px;height:22px;background:var(--blue)}
.brand-name{font-size:30px;font-weight:800;color:var(--ink);letter-spacing:1px}
.brand-tag{font-size:11px;color:var(--blue);line-height:1.15;margin-left:6px;width:110px}
.headline{position:absolute;left:28px;top:104px;font-size:26px;font-weight:800;color:var(--blue);line-height:1.1;white-space:nowrap}
.intro{position:absolute;left:28px;top:172px;width:425px;font-size:15px;line-height:1.35;color:var(--text)}
.tagline{position:absolute;left:28px;top:518px;font-size:20px;font-weight:700;color:#fff;line-height:1.25}
.trades-label{position:absolute;left:478px;top:228px;background:var(--sky);color:#fff;font-weight:800;font-size:19px;padding:3px 10px}
.trades-intro{position:absolute;left:482px;top:268px;width:258px;color:#fff;font-size:14.5px;line-height:1.3}
.trade-list{position:absolute;left:482px;top:346px;width:260px;display:grid;grid-template-columns:1fr 1fr;column-gap:10px;row-gap:4px;list-style:none;color:#fff;font-size:14.5px;line-height:1.2}
.trade-list li::before{content:"• ";}
.quote-cta{position:absolute;left:472px;top:518px;color:#fff;font-weight:800;font-size:20px}
.register{position:absolute;left:458px;top:552px;width:292px;background:var(--blue);color:#fff;font-size:14px;font-weight:600;padding:4px 10px}
.easy{position:absolute;left:26px;top:160px;color:#fff}
.easy h2{font-size:38px;font-weight:700;line-height:1.1;margin-bottom:8px}
.easy p{font-size:28px;line-height:1.18}
.no-obligation{position:absolute;left:26px;top:348px;color:var(--pale);font-size:18px;letter-spacing:1px;font-weight:600}
.contact{position:absolute;left:26px;top:405px;color:#fff;font-size:15px;line-height:1.3}
.stamp{position:absolute;left:608px;top:48px;width:92px;height:88px;border:2px solid #777}
.address-line{position:absolute;left:440px;width:262px;height:0;border-top:2px solid #888}
</style>
</head>
<body>

<section class="card front">
  <svg class="art" width="750" height="590" viewBox="0 0 750 590">
    <defs>
      <linearGradient id="siteGrad" x1="0" y1="0" x2="1" y2="1">
        <stop offset="0" stop-color="#9fb5c8"/>
        <stop offset="0.5" stop-color="#7d8f9c"/>
        <stop offset="1" stop-color="#2c3f55"/>
      </linearGradient>
      <linearGradient id="roofGrad" x1="0" y1="0" x2="1" y2="1">
        <stop offset="0" stop-color="#8fb9dc"/>
        <stop offset="1" stop-color="#3b5a7a"/>
      </linearGradient>
      <clipPath id="panelClip"><polygon points="488,0 750,0 750,590 452,590"/></clipPath>
    </defs>
    <rect role="img" aria-label="Photo of blueprints, a yellow hard hat and a tablet in front of a city construction skyline" x="0" y="330" width="480" height="260" fill="url(#siteGrad)"/>
    <polygon points="488,0 750,0 750,590 452,590" fill="var(--ink)"/>
    <g clip-path="url(#panelClip)">
      <rect role="img" aria-label="Photo of a roofer working on a commercial roof" x="440" y="0" width="320" height="220" fill="url(#roofGrad)"/>
    </g>
  </svg>

  <div class="brand">
    <span class="brand-mark"></span>
    <span class="brand-name">BRINDLE QUANTS</span>
    <span class="brand-tag">Commercial Construction Professionals</span>
  </div>
  <h1 class="headline">COMMERCIAL CONSTRUCTION<br>TAKEOFF SERVICES</h1>
  <p class="intro">We provide a service for our customers who don't have enough time to handle their full inbox of RFP's and Bid Requests. We will read the blueprints, specs, and notes for you and provide you with everything your estimator needs: quantities, area, notes, etc. We provide this service for most commercial construction trades!</p>
  <p class="tagline">Affordable, Professional<br>Commercial Blueprint Quantity Takeoffs</p>

  <div class="trades-label">TRADES SERVICED</div>
  <p class="trades-intro">Our experts will assist you with commercial quantity takeoffs for most construction trades including:</p>
  <ul class="trade-list">
    <li>Floor &amp; Wallcoverings</li>
    <li>Roofing</li>
    <li>Painting</li>
    <li>Siding</li>
    <li>Sheetrock</li>
    <li>Foundations &amp; Paving</li>
  </ul>
  <p class="quote-cta">Get a FREE Quote</p>
  <p class="register">Register @ www.brindlequants.com</p>
</section>

<section class="card back">
  <svg class="art" width="750" height="510" viewBox="0 0 750 510">
    <defs>
      <linearGradient id="teamGrad" x1="0" y1="0" x2="1" y2="1">
        <stop offset="0" stop-color="#27558a"/>
        <stop offset="0.6" stop-color="#16345c"/>
        <stop offset="1" stop-color="#0d2140"/>
      </linearGradient>
    </defs>
    <polygon role="img" aria-label="Photo of contractors reviewing construction plans together, with a blue overlay" points="0,100 420,100 385,510 0,510" fill="url(#teamGrad)"/>
    <polygon points="300,100 420,100 405,270" fill="#6f8fb3" opacity="0.6"/>
  </svg>

  <div class="brand">
    <span class="brand-mark"></span>
    <span class="brand-name">BRINDLE QUANTS</span>
    <span class="brand-tag">Commercial Construction Professionals</span>
  </div>

  <div class="easy">
    <h2>It's so EASY!!!</h2>
    <p>You load your plans<br>We give you a quote<br>If you approve,<br>we do the work!</p>
  </div>
  <p class="no-obligation">NO OBLIGATION TO PURCHASE</p>
  <p class="contact">Contact Us<br>Mark Ellison, Owner<br>555-014-2290<br>mark@brindlequants.com</p>

  <div class="stamp"></div>
  <div class="address-line" style="top:295px"></div>
  <div class="address-line" style="top:348px"></div>
  <div class="address-line" style="top:402px"></div>
  <div class="address-line" style="top:456px"></div>
</section>

</body>
</html>
```